Website Performance Testing eBook for the software testing industry

Overview:
I would like an ebook/whitepaper designed. This ebook will be digital published on my website as a lead generation piece. The purpose is to give high level tips on what to look for and things to think about when working on a website performance testing project.
The ebook also demonstrates our expertise and knowledge on the topic.
Topic:
This is an ebook on software testing. Specifically, website performance testing.
About Veltrana:
Veltrana Solutions is an outsourcing development and software testing firm, and we provide expert services for application development, testing and data analytics. We extend our clients’ software testing capabilities with on-demand technical expertise. Our quality assurance resources work as part of our clients’ teams to help test applications on time and within budget.
Our model is designed to allocate the right mix of local and offshore resources in order to optimize expertise, speed and cost. We provide the ability to quickly add specialty skills to our client’s development team without them incurring long-term costs. The result is far better management of resource capacities and outcomes.
Background on our branding and previous pieces:
I have included a few of our previous ebooks and whitepapers. I like the look and feel of these pieces, however we have made updates to our brand guidelines since them, so the new brand guidelines will need to be incorporated, and I'd like to refresh/update what we have done in the past.
Refer to our website for an idea of our look and feel. This page is one of our newer sections and would be a good reference:
http://www.veltranasol.example/data-analytics/
Tone and feel:
- The look and feel should be professional, clean and polished.
- I like good use of whitespace.
- I would prefer to keep stock photography of people to a minimum. Any images should add to the content and be relevant to the content.
(Also, I uploaded some InDesign files in case you wanted to refer to those assets, but I didn't include the Links folder because they were too big. If there's anything you more you need, let me know)
Target Market(s)
Audience:
The audience is senior Quality Assurance and Software Testing professionals.
- 30-45 years old
- Technical mindset
- Interested in learning
Titles include
- QA Lead
- QA Manager
- QA Director
- Director or VP of Development
- QA Automation Engineer
Our customers are medium to large sized companies. Many are software companies, but many are also enterprises in all almost all industries.

```html
<!DOCTYPE html>
<html lang="en">
<head>
<meta charset="utf-8">
<title>Website Performance Testing – Why Use the Cloud</title>
<link rel="stylesheet" href="https://fonts.googleapis.com/css2?family=Open+Sans:wght@300;400;600&display=swap">
<style>
  :root {
    --brand-red: #e8392a;
    --bullet-red: #f0412f;
    --text-grey: #6a6a6a;
    --rule-grey: #c9c9c9;
    --logo-grey: #9a9a9a;
    --page-bg: #ffffff;
  }
  * { margin: 0; padding: 0; box-sizing: border-box; }
  html, body { width: 927px; height: 1200px; overflow: hidden; background: var(--page-bg); }
  body { font-family: "Open Sans", sans-serif; font-weight: 300; color: var(--text-grey); position: relative; }

  .page-header {
    position: absolute; left: 54px; top: 60px; width: 820px; height: 49px;
    border-bottom: 1px solid var(--rule-grey);
  }
  .running-title { position: absolute; left: 0; top: 14px; font-size: 14px; font-weight: 400; color: var(--text-grey); }
  .brand { position: absolute; right: 12px; top: 0; text-align: right; line-height: 1; }
  .brand-name { display: block; font-size: 26px; font-weight: 400; color: var(--brand-red); letter-spacing: 0.2px; }
  .brand-sub { display: block; font-size: 13px; font-weight: 400; color: var(--logo-grey); margin-top: 1px; }

  .section-heading {
    position: absolute; left: 97px; top: 166px; height: 106px;
    border-left: 2px solid var(--brand-red); padding-left: 29px; padding-top: 14px;
  }
  .section-heading h1 {
    font-size: 37.5px; font-weight: 300; color: var(--brand-red);
    line-height: 38px; letter-spacing: 0.2px; text-transform: uppercase;
  }

  .intro, .outro { position: absolute; left: 109px; width: 720px; font-size: 15.5px; line-height: 21.5px; }
  .intro { top: 322px; }
  .outro { top: 801px; }

  .benefits { list-style: none; position: absolute; left: 97px; top: 433px; width: 730px; }
  .benefits li { position: absolute; left: 0; width: 730px; font-size: 15.5px; line-height: 21.5px; padding-left: 67px; }
  .benefits li::before {
    content: ""; position: absolute; left: 0; top: 3px;
    width: 12px; height: 12px; border-radius: 50%; background: var(--bullet-red);
  }

  .page-number { position: absolute; left: 818px; top: 1124px; font-size: 16px; font-weight: 400; color: var(--brand-red); }
</style>
</head>
<body>
  <header class="page-header">
    <span class="running-title">Website Performance Testing</span>
    <div class="brand">
      <span class="brand-name">veltrana</span>
      <span class="brand-sub">solutions</span>
    </div>
  </header>

  <div class="section-heading">
    <h1>Why use the cloud for website<br>performance testing</h1>
  </div>

  <p class="intro">Website performance testing utilizing cloud-based tools and infrastructure offers many of the same advantages as cloud-based enterprise apps, such as cost reduction, faster test deployment and dynamic scaling:</p>

  <ul class="benefits">
    <li style="top:0">Minimizes capital expense for on-site hardware and infrastructure while reducing ongoing costs for maintenance.</li>
    <li style="top:95px">Eliminates long hardware acquisition lead times.</li>
    <li style="top:163px">Offers choice in selecting vendor features most important to your website testing.</li>
    <li style="top:231px">Provides immediate scalability to meet your performance testing scenarios.</li>
    <li style="top:299px">Eliminates disruptions due to equipment failure or power outages.</li>
  </ul>

  <p class="outro">Additionally, the cloud provides specific benefits that increase the accuracy and efficiency for website performance testing.</p>

  <div class="page-number">6</div>
</body>
</html>
```